Simple Business Card Design for Tavlo

Job:

Make a very simple, minimalist business card design with my details including adjusted logo. One side to be white (with logo & text). Other side to be yellow - try plain or with logo (or part of logo eg Z). Need business card to have continuity with website.

Logo:
Our logo is made from a free download font website:
http://www.typewell.net/search.php?q=rubber
but the spacing/kerning needs correcting/adjusting as the font spaces unevenly between letters (see attached files). Need logo to be very crisp/sharp when printed.

Printing:
We will be using Plika.com so the design needs to conform to their requirements, see here:

http://uk.plika.com/products/luxe/business-cards.html (scroll down for dimensions and guidelines)

Design:

must say "plant-based food consulting" underneath logo or somewhere
no address needed in contact section
sharp corners (not rounded)
one side white, one side yellow

name: Rosalind Whitcombe
1xmobile number: +44 7700900463
1xtwiiter: @brimcounsel
website address www.orchardtable.com
email address brim@orchardtable.com

Should be easy quick job, prompt + detailed feedback given, am online in UK 9am-10pm for next 3 days. Website is www.orchardtable.com

Industry/Entity Type

Business

Requirements
Must have
• The logo must be corrected. The kerning is not right.

Please use a warm-grey for text

Please submit in matt format, we will be printing matt finish.

Should not have
• Avoid using banners or curvy highlights

Please avoid using black

Please avoid submitting in gloss finish

```html
<!DOCTYPE html>
<html lang="en">
<head>
<meta charset="utf-8">
<title>Tavlo business card</title>
<link rel="stylesheet" href="https://fonts.googleapis.com/css2?family=Arimo:wght@400;700&family=Questrial&display=swap">
<style>
  :root {
    --stage-grey: #5b5b5b;
    --stage-white: #ffffff;
    --card-white: #f7f7f6;
    --brand-yellow: #fde630;
    --brand-yellow-deep: #f2d92a;
    --warm-grey: #5e5a56;
    --divider: #d9d7d4;
    --trim-orange: #f08a24;
    --bleed-dash: #6b6b6b;
  }
  * { margin: 0; padding: 0; box-sizing: border-box; }
  html, body { width: 1200px; height: 1000px; overflow: hidden; }
  body { position: relative; background: var(--stage-white); font-family: "Arimo", Arial, sans-serif; }

  .band { position: absolute; left: 0; width: 1200px; }
  .band--top { top: 0; height: 395px; background: var(--stage-grey); }
  .band--middle { top: 395px; height: 193px; background: var(--stage-white); }
  .band--bottom { top: 588px; height: 412px; background: var(--stage-grey); }

  .card { position: absolute; }
  .card--front { background: var(--card-white); }
  .card--back { background: var(--brand-yellow-deep); }
  .card--template.card--front { background: var(--stage-white); }
  .card--template.card--back { background: var(--brand-yellow); }

  .wordmark {
    position: absolute; font-family: "Arimo", Arial, sans-serif; font-weight: 700;
    color: var(--brand-yellow); letter-spacing: 2px; line-height: 1;
  }
  .wordmark--card { font-size: 46px; }
  .wordmark--reversed { color: var(--stage-white); }
  .wordmark--hero { font-size: 76px; left: 0; width: 1200px; text-align: center; top: 454px; letter-spacing: 4px; }

  .tagline {
    position: absolute; width: 170px; text-align: right;
    font-size: 11px; line-height: 13px; color: var(--warm-grey); text-transform: uppercase;
  }
  .divider { position: absolute; width: 1px; background: var(--divider); }
  .holder-name { position: absolute; font-size: 14px; font-weight: 700; color: var(--warm-grey); letter-spacing: .3px; }
  .contact-list { position: absolute; list-style: none; }
  .contact-list li { display: flex; align-items: center; height: 15.5px; font-size: 11px; color: var(--warm-grey); }
  .contact-list svg { width: 10px; height: 10px; margin-right: 6px; flex: none; }

  .bleed-line { position: absolute; border: 1px dashed var(--bleed-dash); }
  .trim-line { position: absolute; border: 1.5px solid var(--trim-orange); }

  .template-label {
    position: absolute; left: 42px; top: 920px; transform: rotate(-90deg); transform-origin: left top;
    font-family: "Questrial", "Century Gothic", sans-serif; font-size: 18px; color: var(--stage-white); white-space: nowrap;
  }
</style>
</head>
<body>
  <div class="band band--top"></div>
  <div class="band band--middle"></div>
  <div class="band band--bottom"></div>

  <svg width="0" height="0" style="position:absolute">
    <defs>
      <symbol id="icon-phone" viewBox="0 0 10 10"><circle cx="5" cy="5" r="4.4" fill="none" stroke="#fde630" stroke-width="1"/><path d="M3.3 2.8c.3-.3.6-.2.8.1l.4.6c.1.2 0 .4-.2.5l-.2.2c.3.6.7 1 1.3 1.3l.2-.2c.1-.2.3-.3.5-.2l.6.4c.3.2.4.5.1.8-.4.4-1 .5-1.6.2C4.3 6.1 3.6 5.4 3.2 4.5c-.3-.6-.3-1.3.1-1.7z" fill="#fde630"/></symbol>
      <symbol id="icon-handle" viewBox="0 0 10 10"><circle cx="5" cy="5" r="4.4" fill="#fde630"/></symbol>
      <symbol id="icon-mail" viewBox="0 0 10 10"><circle cx="5" cy="5" r="4.4" fill="none" stroke="#fde630" stroke-width="1"/><rect x="2.8" y="3.4" width="4.4" height="3.2" fill="none" stroke="#fde630" stroke-width=".8"/><path d="M2.8 3.4 5 5.2l2.2-1.8" fill="none" stroke="#fde630" stroke-width=".8"/></symbol>
      <symbol id="icon-web" viewBox="0 0 10 10"><circle cx="5" cy="5" r="4.4" fill="none" stroke="#fde630" stroke-width="1"/><ellipse cx="5" cy="5" rx="1.6" ry="3.4" fill="none" stroke="#fde630" stroke-width=".7"/><path d="M1.6 5h6.8" stroke="#fde630" stroke-width=".7"/></symbol>
    </defs>
  </svg>

  <!-- Finished cards -->
  <section class="card card--front" style="left:131px;top:66px;width:425px;height:279px">
    <div class="wordmark wordmark--card" style="left:40px;top:95px">TAVLO</div>
    <p class="tagline" style="left:-5px;top:168px">Plant-based<br>food consulting</p>
    <div class="divider" style="left:200px;top:62px;height:157px"></div>
    <h2 class="holder-name" style="left:229px;top:97px">ROSALIND WHITCOMBE</h2>
    <ul class="contact-list" style="left:229px;top:133px">
      <li><svg><use href="#icon-phone"/></svg>+44 7700900463</li>
      <li><svg><use href="#icon-handle"/></svg>@brimcounsel</li>
      <li><svg><use href="#icon-mail"/></svg>brim@orchardtable.com</li>
      <li><svg><use href="#icon-web"/></svg>www.orchardtable.com</li>
    </ul>
  </section>

  <section class="card card--back" style="left:651px;top:66px;width:425px;height:279px">
    <div class="wordmark wordmark--card wordmark--reversed" style="left:0;width:425px;text-align:center;top:116px;font-size:44px">TAVLO</div>
  </section>

  <!-- Logo -->
  <div class="wordmark wordmark--hero">TAVLO</div>

  <!-- Print template -->
  <section class="card card--template card--front" style="left:120px;top:639px;width:447px;height:300px">
    <div class="bleed-line" style="left:11px;top:11px;width:425px;height:279px"></div>
    <div class="trim-line" style="left:21px;top:21px;width:405px;height:259px"></div>
    <div class="wordmark wordmark--card" style="left:51px;top:106px">TAVLO</div>
    <p class="tagline" style="left:6px;top:179px">Plant-based<br>food consulting</p>
    <div class="divider" style="left:211px;top:62px;height:178px"></div>
    <h2 class="holder-name" style="left:240px;top:106px">ROSALIND WHITCOMBE</h2>
    <ul class="contact-list" style="left:240px;top:143px">
      <li><svg><use href="#icon-phone"/></svg>+44 7700900463</li>
      <li><svg><use href="#icon-handle"/></svg>@brimcounsel</li>
      <li><svg><use href="#icon-mail"/></svg>brim@orchardtable.com</li>
      <li><svg><use href="#icon-web"/></svg>www.orchardtable.com</li>
    </ul>
  </section>

  <section class="card card--template card--back" style="left:641px;top:639px;width:445px;height:300px">
    <div class="bleed-line" style="left:10px;top:11px;width:425px;height:279px"></div>
    <div class="trim-line" style="left:10px;top:21px;width:425px;height:259px;border-left:none;border-right:none"></div>
    <div class="wordmark wordmark--card wordmark--reversed" style="left:0;width:445px;text-align:center;top:128px;font-size:44px">TAVLO</div>
  </section>

  <p class="template-label">PLIKA Business card template</p>
</body>
</html>
```